Brightway Haus Inc. Business Card Design

Brightway Haus Inc. is in search of a great clean design for our business cards!

Looking to incorporate our full logo and watermark on side one (however, I am open to having the text and watermark separated within the design.)

On side two, I am looking to have contact information (Name, Position, Phone #, Email, Website (www.thebrightwayhaus.ca). Can have the logo and/or watermark as part of the design if applicable.

Please add tagline "Where Shine Counts" on either side 1 or 2. This tagline can be in a sans serif, serif or cursive font as long as it compliments overall design. Capitalization can be title or sentence case depending on how it fits within the design.

Get creative!! Looking for a clean, crisp, premium design! Looking for a glossy card finish with spot UV features when printed. Cards will also be printed with rounded corners. Standard dimensions (3.5 x 2).

Target Market(s)

B2B - primary clients are business owners or property management corporations. (residential jobs are few and far between)

Industry/Entity Type

Business

Contact Information for Business Card

- clean, crisp design
- double sided
- spot UV accents and glossy finish upon printing
- standard business card size (3.5 x 2) with rounded corners
- please see project description for requirements per side

Font styles to use
Sans Serif

Requirements
Must have
• - adequate bleeds with print ready files
• - cohesive design elements between side 1 & 2
• - spot UV elements (can be on both sides or just one, use your discretion)
• - colour pallet should match the logo file provided
• - incorporate tagline "where shine counts" (this tagline can be in a serif or sans serif font as long as it is complimentary to the overall design.
Nice to have
• - Premium elements with a clean design
Should not have
• - Please omit cartoon or whimsical like designs, think premium.
• - Colours should not stray from the pallet of the provided logo.

```html
<!DOCTYPE html>
<html lang="en">
<head>
<meta charset="utf-8">
<title>Brightway Haus Inc. — Business Card</title>
<link href="https://fonts.googleapis.com/css2?family=Open+Sans:wght@800&family=Roboto:wght@400;500;700&display=swap" rel="stylesheet">
<style>
  :root {
    --teal: #11999a;
    --navy: #1c1d45;
    --grey: #9a9a9a;
    --ink: #2a2a2a;
    --card-top: #f3f3f3;
    --card-bottom: #dedede;
    --stage: #e8e8e8;
    --white: #ffffff;
  }
  * { margin: 0; padding: 0; box-sizing: border-box; }
  html, body {
    width: 1200px; height: 576px; overflow: hidden;
    background: var(--stage);
    font-family: "Roboto", Arial, sans-serif;
  }
  .stage { position: relative; width: 1200px; height: 576px; }
  .card {
    position: absolute; top: 138px; width: 484px; height: 294px;
    border-radius: 12px; overflow: hidden;
    background: linear-gradient(160deg, var(--card-top), var(--card-bottom));
    box-shadow: 0 2px 6px rgba(0,0,0,0.18);
  }
  .card--front { left: 82px; }
  .card--back { left: 602px; }

  .wordmark {
    display: flex; align-items: center; gap: 10px;
    font-family: "Open Sans", Arial, sans-serif; font-weight: 800;
    color: var(--navy); letter-spacing: -0.5px; white-space: nowrap;
  }
  .wordmark__square { width: 26px; height: 26px; background: var(--teal); flex: none; }
  .card--front .wordmark {
    position: absolute; left: 0; right: 0; top: 126px;
    justify-content: center; font-size: 34px;
  }
  .card--back .wordmark {
    position: absolute; left: 28px; top: 44px; font-size: 31px;
  }

  .edge-tab {
    position: absolute; left: -16px; top: 130px;
    width: 30px; height: 30px; border-radius: 50%; background: var(--teal);
  }
  .person { position: absolute; left: 26px; top: 133px; }
  .person__name { font-size: 21px; font-weight: 700; color: var(--teal); }
  .person__role { font-size: 12px; color: var(--ink); margin-top: 6px; }

  .contacts { position: absolute; left: 26px; top: 199px; list-style: none; }
  .contacts li {
    display: flex; align-items: center; gap: 10px;
    font-size: 13px; color: var(--ink); height: 18px;
  }
  .contacts svg { width: 11px; height: 11px; fill: var(--teal); flex: none; }
  .contacts .accent { color: var(--teal); }

  .address {
    position: absolute; right: 26px; top: 199px; text-align: right;
    font-size: 13px; line-height: 17px; color: var(--ink); font-style: normal;
  }

  .band {
    position: absolute; left: 0; bottom: 0; width: 290px; height: 12px;
    background: var(--teal);
  }
  .tagline-block {
    position: absolute; right: 0; bottom: 0; width: 204px; height: 29px;
    background: var(--navy);
    clip-path: polygon(16px 0, 100% 0, 100% 100%, 0 100%);
    display: flex; align-items: center; justify-content: flex-end; padding-right: 14px;
    color: var(--white); font-size: 11.5px; letter-spacing: 0.8px;
  }
</style>
</head>
<body>
<main class="stage">

  <section class="card card--front" aria-label="Card front">
    <div class="wordmark"><span class="wordmark__square"></span>BRIGHTWAY HAUS INC.</div>
  </section>

  <section class="card card--back" aria-label="Card back">
    <div class="wordmark"><span class="wordmark__square"></span>BRIGHTWAY HAUS INC.</div>

    <span class="edge-tab"></span>
    <div class="person">
      <h1 class="person__name">Marcus Hale</h1>
      <p class="person__role">Managing Director</p>
    </div>

    <ul class="contacts">
      <li>
        <svg viewBox="0 0 12 12"><path d="M1 3.2C1 2 2.5 1 6 1s5 1 5 2.2V4.3H8.3V3.2H3.7v1.1H1zM2.6 5h6.8L11 8.6V11H1V8.6zM6 6.6a1.4 1.4 0 1 0 0 2.8 1.4 1.4 0 0 0 0-2.8z"/></svg>
        1800-555-0147
      </li>
      <li>
        <svg viewBox="0 0 12 12"><path d="M0 2h12v1.2L6 7 0 3.2zM0 4.6l6 3.8 6-3.8V10H0z"/></svg>
        marcus@brightwayhaus.ca
      </li>
      <li>
        <svg viewBox="0 0 12 12"><path d="M6 0a6 6 0 1 0 0 12A6 6 0 0 0 6 0zm4.8 5.3H8.6A9 9 0 0 0 7.7 1.4a4.9 4.9 0 0 1 3.1 3.9zM6 1.2c.8.9 1.4 2.3 1.5 4.1h-3C4.6 3.5 5.2 2.1 6 1.2zM4.3 1.4a9 9 0 0 0-.9 3.9H1.2a4.9 4.9 0 0 1 3.1-3.9zM1.2 6.7h2.2a9 9 0 0 0 .9 3.9 4.9 4.9 0 0 1-3.1-3.9zM6 10.8c-.8-.9-1.4-2.3-1.5-4.1h3c-.1 1.8-.7 3.2-1.5 4.1zm1.7-.2a9 9 0 0 0 .9-3.9h2.2a4.9 4.9 0 0 1-3.1 3.9z"/></svg>
        <span>www.<span class="accent">thebrightwayhaus</span>.ca</span>
      </li>
    </ul>

    <address class="address">48 Harbour Lane<br>Toronto, ON M5V 2T6</address>

    <div class="band"></div>
    <p class="tagline-block">Where Shine Counts</p>
  </section>

</main>
</body>
</html>
```